Caldrift - Where every box finds its place!

Hello,
I'd like to update, re-vamp, and re-tool this current power point presentation with slightly more professional appearance as well as more accurately reflect the website -caldrift.com- color scheme and sleek design scheme. Please see attached.
We at Caldrift pride ourselves on seeking to rework an archaic business into something progressive, cost effective, more reliable, and easily accessible in todays fast growing market that has only gotten more expensive, more costly and less indirect over the last couple years.

Target Market(s)

New updated and hassle free moving opportunities no matter how large or how small in a market that begs for a change

Industry/Entity Type

Logistics/Moving

Requirements
Must have
• The current color scheme from the -caldrift.com- website as well as the inclusion of the current data on the sample power point presentation provided but with updated graphics

```html
<!DOCTYPE html>
<html lang="en">
<head>
<meta charset="utf-8">
<title>Caldrift – Presentation</title>
<link rel="stylesheet" href="https://fonts.googleapis.com/css2?family=Montserrat:wght@400;500;600;700;800;900&display=swap">
<style>
:root{
  --navy:#0d3b8e;
  --navy-dark:#082a68;
  --yellow:#fcc21b;
  --ink:#1f2430;
  --grey-band:#2d2d2f;
  --page:#eef0f3;
  --muted:#5a6172;
  --ice:#e3eefa;
  --step:#dfe3ea;
}
*{margin:0;padding:0;box-sizing:border-box}
html,body{width:1200px;height:4284px;overflow:hidden}
body{background:var(--page);font-family:'Montserrat',sans-serif;color:var(--ink);position:relative}
.slide{position:absolute;left:40px;width:1120px;height:630px;background:#fff;overflow:hidden;box-shadow:0 4px 18px rgba(0,0,0,.08)}
.abs{position:absolute}
.photo{position:absolute}

/* cover */
.cover{top:110px}
.cover .photo{left:0;top:0;width:600px;height:630px;background:linear-gradient(135deg,#c9d3de 0%,#8d9aab 45%,#e9edf2 100%)}
.cover .panel{left:600px;top:0;width:520px;height:630px;background:var(--navy)}
.cover .corner{right:0;top:0}
.cover .foot-bar{left:0;bottom:0}
.brand{left:660px;top:150px;display:flex;align-items:center;gap:18px}
.brand .mark{width:44px;height:44px;background:var(--yellow)}
.brand .name{font-weight:800;font-size:72px;color:#fff;letter-spacing:-1px}
.cover .tagline{left:664px;top:262px;color:var(--yellow);font-weight:800;font-size:18px;letter-spacing:.3px;white-space:nowrap}
.cover .url{left:664px;top:520px;color:#fff;font-weight:700;font-size:20px;letter-spacing:1px}

/* about */
.about{top:802px}
.about .band{left:0;top:0;width:1120px;height:64px;background:var(--grey-band)}
.about .card{left:70px;top:110px;width:900px;height:360px;background:var(--yellow)}
.about h2{left:105px;top:150px;color:var(--navy);font-size:40px;font-weight:800}
.about p{left:105px;top:220px;width:430px;font-size:14.5px;line-height:1.55;color:var(--navy-dark);font-weight:500}
.about .frame{left:580px;top:78px;width:430px;height:330px;border:8px solid var(--navy);background:#fff}
.about .photo{left:0;top:0;width:100%;height:100%;background:linear-gradient(135deg,#d9a574 0%,#7b4a33 50%,#e8d6c2 100%)}

/* problems */
.problems{top:1494px}
.section-title{left:0;width:100%;text-align:center;color:var(--navy);font-size:36px;font-weight:800}
.problems .section-title{top:72px}
.problems .base{left:0;bottom:0;width:1120px;height:56px;background:var(--yellow)}
.problems .base-line{left:0;bottom:56px;width:1120px;height:10px;background:#f4f5f7}
.step-num{position:absolute;top:128px;font-size:84px;font-weight:800;color:var(--step);line-height:1;z-index:1}
.wave{left:0;top:250px;z-index:1}
.issue{position:absolute;z-index:2;top:190px;width:200px;height:200px;border-radius:50%;background:#fff;box-shadow:0 6px 18px rgba(13,59,142,.18);border:3px solid #e9ecf2;text-align:center;padding:24px 20px 0}
.issue svg{width:44px;height:44px;margin-bottom:8px}
.issue p{font-size:11.5px;line-height:1.4;font-weight:500;color:var(--ink)}

/* solution */
.solution{top:2186px;background:linear-gradient(120deg,#f3f8fd 0%,var(--ice) 60%,#cfe1f4 100%)}
.solution .section-title{top:50px}
.item{position:absolute;width:440px;display:flex;gap:18px}
.item .ico{flex:0 0 54px;height:54px;border-radius:10px;background:var(--yellow);display:flex;align-items:center;justify-content:center}
.item .ico svg{width:30px;height:30px}
.item h3{font-size:15px;font-weight:800;color:var(--navy);margin-bottom:6px;letter-spacing:.3px}
.item p{font-size:12.5px;line-height:1.45;color:var(--ink);font-weight:500}
.pill{left:600px;top:470px;width:430px;height:70px;border-radius:35px;background:var(--navy);display:flex;align-items:center;gap:16px;padding-left:8px}
.pill .badge{width:56px;height:56px;border-radius:50%;background:var(--yellow)}
.pill span{color:var(--yellow);font-size:14px;font-weight:700;line-height:1.35}

/* questions */
.questions{top:2878px}
.questions .band{left:0;top:0;width:1120px;height:110px;background:var(--navy)}
.questions .band-edge{left:0;top:110px;width:1120px;height:12px;background:#d8e2f0}
.questions .section-title{top:168px}
.questions .portrait{left:280px;top:330px;width:540px;height:300px;background:linear-gradient(160deg,#f0e6dc 0%,#c89b7b 55%,#efe9e3 100%)}
.questions .deco-dark{left:80px;top:250px;width:110px;height:150px;border-radius:14px;background:#2c2f36}
.questions .deco-yellow{left:880px;top:320px;width:170px;height:250px;border-radius:18px;background:var(--yellow)}

/* thanks */
.thanks{top:3570px}
.thanks .panel{left:0;top:0;width:480px;height:630px;background:var(--navy)}
.thanks .corner{left:0;bottom:0}
.thanks .photo{left:480px;top:0;width:640px;height:630px;background:linear-gradient(135deg,#8fc6e4 0%,#f6d36b 35%,#f39a4d 60%,#9a6cc7 100%)}
.thanks h2{left:535px;top:265px;font-size:80px;font-weight:800;color:#2a2a30;white-space:nowrap}
.contacts{left:80px;top:230px;color:#fff;font-size:15px;font-weight:600;line-height:1.45}
.contacts li{list-style:none;display:flex;gap:16px;align-items:flex-start;margin-bottom:26px}
.contacts svg{flex:0 0 20px;width:20px;height:20px;margin-top:1px}

.legal{position:absolute;top:4240px;left:40px;right:40px;display:flex;justify-content:space-between;font-size:12px;color:var(--muted)}
</style>
</head>
<body>

<section class="slide cover">
  <div class="photo" role="img" aria-label="Business partners shaking hands in front of a city skyline"></div>
  <div class="abs panel"></div>
  <svg class="abs corner" width="180" height="120" viewBox="0 0 180 120"><polygon points="0,0 180,0 180,120" fill="#fcc21b"/></svg>
  <svg class="abs foot-bar" width="300" height="70" viewBox="0 0 300 70"><polygon points="0,0 240,0 300,70 0,70" fill="#fcc21b"/></svg>
  <div class="abs brand"><span class="mark"></span><span class="name">Caldrift</span></div>
  <div class="abs tagline">MOVING FOR THE NEXT GENERATION</div>
  <div class="abs url">WWW.CALDRIFT.COM</div>
</section>

<section class="slide about">
  <div class="abs band"></div>
  <div class="abs card"></div>
  <h2 class="abs">ABOUT US</h2>
  <p class="abs">Caldrift is the next logical evolution in professional moving. Professional moving clients have battled soaring prices, acute capacity problems and deteriorating service levels. Caldrift was founded by lifelong moving professionals who have developed the answer to better moving services. Poised as the industry disrupter, we deliver faster, offer guaranteed prices and even offer no credit check financing options. We are a technology first organization using proprietary software to deliver moving's best service experience.</p>
  <div class="abs frame"><div class="photo" role="img" aria-label="Family sitting among moving boxes in their new home"></div></div>
</section>

<section class="slide problems">
  <h2 class="abs section-title">MOVING'S PROBLEMS</h2>
  <span class="step-num" style="left:70px">01</span>
  <span class="step-num" style="left:320px">02</span>
  <span class="step-num" style="left:570px">03</span>
  <span class="step-num" style="left:820px">04</span>
  <svg class="abs wave" width="1120" height="120" viewBox="0 0 1120 120"><path d="M40 60 C 130 0, 230 120, 330 60 S 530 0, 560 60 S 730 120, 800 60 S 990 0, 1080 60" fill="none" stroke="#2c2f36" stroke-width="3"/></svg>
  <div class="issue" style="left:90px">
    <svg viewBox="0 0 24 24" fill="none" stroke="#1f2430" stroke-width="2"><circle cx="12" cy="12" r="9"/><path d="M12 7v10M9 9.5h4.5a1.75 1.75 0 010 3.5h-3a1.75 1.75 0 000 3.5H15"/></svg>
    <p>Moving cost has skyrocketed over the last three years. Charges have increased 38% since 2019.</p></div>
  <div class="issue" style="left:340px">
    <svg viewBox="0 0 24 24" fill="none" stroke="#1f2430" stroke-width="2"><rect x="2" y="7" width="12" height="9"/><path d="M14 10h4l3 3v3h-7z"/><circle cx="7" cy="18" r="1.8"/><circle cx="17" cy="18" r="1.8"/></svg>
    <p>Long-haul driver shortages and limited equipment coupled with growing demand has pushed capacity to a crisis state.</p></div>
  <div class="issue" style="left:590px">
    <svg viewBox="0 0 24 24" fill="none" stroke="#1f2430" stroke-width="2"><circle cx="12" cy="8" r="4"/><path d="M4 21c0-4.4 3.6-7 8-7s8 2.6 8 7"/></svg>
    <p>Quality labor has been difficult to source and afford. Virtually all review sites report a decline in service quality.</p></div>
  <div class="issue" style="left:840px">
    <svg viewBox="0 0 24 24" fill="none" stroke="#1f2430" stroke-width="2"><circle cx="10" cy="10" r="6"/><path d="M14.5 14.5L21 21"/></svg>
    <p>Too many moving layers, van line, agent, driver and help. In addition, charges are convoluted and hidden.</p></div>
  <div class="abs base-line"></div>
  <div class="abs base"></div>
</section>

<section class="slide solution">
  <h2 class="abs section-title">SOLUTION</h2>
  <div class="item" style="left:60px;top:130px">
    <div class="ico"><svg viewBox="0 0 24 24" fill="none" stroke="#0d3b8e" stroke-width="2"><path d="M5 12l4 4 10-10"/></svg></div>
    <div><h3>APP-STYLE PROCESS</h3><p>Caldrift automatically qualify: Compliance, Insurance, Regulatory, Bonding, Background checks, and Quality.</p></div></div>
  <div class="item" style="left:60px;top:250px">
    <div class="ico"><svg viewBox="0 0 24 24" fill="none" stroke="#0d3b8e" stroke-width="2"><path d="M5 4h4l2 5-2.5 1.5a11 11 0 005 5L15 13l5 2v4a1 1 0 01-1 1A16 16 0 014 5a1 1 0 011-1z"/></svg></div>
    <div><h3>ONE POINT OF CONTACT</h3><p>Today moves are sold from broker to broker until it's finally sold to a mover. Many entities involved means a confusing line of correspondence for the customer.</p></div></div>
  <div class="item" style="left:60px;top:390px">
    <div class="ico"><svg viewBox="0 0 24 24" fill="none" stroke="#0d3b8e" stroke-width="2"><rect x="3" y="5" width="18" height="16" rx="1"/><path d="M3 10h18M8 3v4M16 3v4"/></svg></div>
    <div><h3>BOOK NOW PAY LATER</h3><p>Moving has a high price tag, but no one has ever offered a pay later solution. Much less a no credit check offer.</p></div></div>
  <div class="item" style="left:600px;top:130px">
    <div class="ico"><svg viewBox="0 0 24 24" fill="none" stroke="#0d3b8e" stroke-width="2"><path d="M12 21s-7-6.2-7-11.5a7 7 0 0114 0C19 14.8 12 21 12 21z"/><circle cx="12" cy="9.5" r="2.5"/></svg></div>
    <div><h3>GPS TRACKING</h3><p>Big online retailers have conditioned consumers to expect real-time tracking of goods. Only Caldrift enables you to track all of your belongings door to door.</p></div></div>
  <div class="item" style="left:600px;top:270px">
    <div class="ico"><svg viewBox="0 0 24 24" fill="none" stroke="#0d3b8e" stroke-width="2"><path d="M3 12l9-9h8v8l-9 9z"/><circle cx="16" cy="8" r="1.5"/></svg></div>
    <div><h3>SIMPLE HONEST PRICING</h3><p>Caldrift's proprietary algorithms and data are backed up by a checks and balances process giving the first instant pricing solution that won't change.</p></div></div>
  <div class="abs pill"><span class="badge"></span><span>Bringing the Customer Experience to the<br>21st Century</span></div>
</section>

<section class="slide questions">
  <div class="abs band"></div>
  <div class="abs band-edge"></div>
  <h2 class="abs section-title">DO YOU HAVE ANY QUESTIONS?</h2>
  <div class="abs deco-dark" role="img" aria-label="Large dark question mark graphic"></div>
  <div class="photo portrait" role="img" aria-label="Smiling woman giving two thumbs up"></div>
  <div class="abs deco-yellow" role="img" aria-label="Large yellow question mark graphic"></div>
</section>

<section class="slide thanks">
  <div class="abs panel"></div>
  <svg class="abs corner" width="160" height="110" viewBox="0 0 160 110"><polygon points="0,0 160,110 0,110" fill="#fcc21b"/></svg>
  <div class="photo" role="img" aria-label="Abstract flowing waves of blue, yellow, orange and purple"></div>
  <ul class="abs contacts">
    <li><svg viewBox="0 0 24 24" fill="none" stroke="#fff" stroke-width="2"><path d="M12 21s-7-6.2-7-11.5a7 7 0 0114 0C19 14.8 12 21 12 21z"/><circle cx="12" cy="9.5" r="2.5"/></svg><span>214 N. HARBOR LANE<br>FAIRMONT CITY, OK 73000</span></li>
    <li><svg viewBox="0 0 24 24" fill="none" stroke="#fff" stroke-width="2"><path d="M5 4h4l2 5-2.5 1.5a11 11 0 005 5L15 13l5 2v4a1 1 0 01-1 1A16 16 0 014 5a1 1 0 011-1z"/></svg><span>(800) 555-0142</span></li>
    <li><svg viewBox="0 0 24 24" fill="none" stroke="#fff" stroke-width="2"><circle cx="12" cy="12" r="9"/><path d="M3 12h18M12 3c3 3.5 3 14.5 0 18M12 3c-3 3.5-3 14.5 0 18"/></svg><span>CALDRIFT.COM<br>SUPPORT@CALDRIFT.COM</span></li>
  </ul>
  <h2 class="abs">THANK YOU!</h2>
</section>

<div class="legal"><span>© 2022 Caldrift.com All Rights Reserved.</span><span>1/6</span></div>

</body>
</html>
```